New Business Card Design Project

We require a business card design for Vexalund, a newly established Indian company.
Our focus is on the development, manufacturing, and export of a diverse array of pharmaceutical products on a global scale. The card should convey a professional appearance, as our primary markets are in Africa, China, and Southeast Asian nations.
We envision a two-sided business card, with the reverse side dedicated to a logo set against a solid color or an elegantly designed pattern. The corners should be rounded. We would appreciate seeing both horizontal and vertical design options. We trust the designer to utilize their expertise in creating this design.

The content for the business card is included in the attached Word file.

Target Market(s)

Our primary markets are in Africa, China, and Southeast Asian, Latin America, Maldives, Sri Lanka

Industry/Entity Type

Pharmaceutical Manufacturing and Export

Contact Information for Business Card

Colors

Designer to choose colors to be used in the design.

Requirements
Must have
• The reverse side of the business card features solely the logo along with the tagline, "Care for Every Day."
Should not have
• The logo should not exceed two instances, encompassing both the front and back sides of the card.

```html
<!DOCTYPE html>
<html lang="en">
<head>
<meta charset="utf-8">
<title>Vexalund Business Card</title>
<link rel="stylesheet" href="https://fonts.googleapis.com/css2?family=Open+Sans:wght@400;600;700;800&display=swap">
<style>
  :root {
    --stage: #232325;
    --card-dark: #1d1d20;
    --brand-blue: #2f9fd3;
    --brand-red: #ef5f4c;
    --ink-light: #eeeeee;
    --radius: 22px;
  }
  * { margin: 0; padding: 0; box-sizing: border-box; }
  html, body {
    width: 1200px; height: 780px; overflow: hidden;
    background: var(--stage);
    font-family: "Open Sans", Arial, sans-serif;
  }
  .card-set {
    position: absolute; inset: 0;
    display: flex; align-items: center; justify-content: center; gap: 48px;
  }
  .card {
    position: relative;
    width: 520px; height: 298px;
    border-radius: var(--radius);
    overflow: hidden;
    box-shadow: 0 14px 30px rgba(0,0,0,.45);
  }

  /* Front */
  .card--front { background: var(--card-dark); }
  .brand-block {
    position: absolute; left: 34px; top: 70px; width: 220px;
    display: flex; align-items: center; gap: 10px;
  }
  .brand-dot {
    width: 14px; height: 14px; border-radius: 50%;
    background: var(--brand-red); flex: none;
  }
  .brand-name {
    font-weight: 800; font-size: 36px; letter-spacing: .5px;
    color: var(--brand-blue); line-height: 1;
  }
  .address {
    position: absolute; left: 34px; bottom: 30px;
    font-size: 12.5px; color: var(--brand-blue);
  }
  .divider { position: absolute; left: 250px; top: 40px; }
  .person {
    position: absolute; left: 300px; top: 62px;
  }
  .person-name { font-size: 22px; line-height: 1.1; white-space: nowrap; }
  .person-name .first { font-weight: 700; color: var(--brand-blue); }
  .person-name .rest { font-weight: 400; color: var(--brand-red); }
  .person-role { font-size: 13px; color: var(--ink-light); margin-top: 2px; }
  .contacts {
    position: absolute; left: 300px; top: 148px;
    list-style: none;
  }
  .contacts li {
    display: flex; align-items: center; gap: 9px;
    font-size: 13px; color: var(--ink-light); margin-bottom: 8px;
  }
  .contacts svg { width: 13px; height: 13px; flex: none; }

  /* Back */
  .card--back {
    background: var(--brand-blue);
    display: flex; flex-direction: column; align-items: center; justify-content: center;
  }
  .back-brand {
    display: flex; align-items: center; gap: 12px;
  }
  .back-brand .brand-dot { background: var(--ink-light); width: 16px; height: 16px; }
  .back-brand .brand-name { color: var(--ink-light); font-size: 50px; }
  .tagline {
    margin-top: 10px; font-size: 13px; color: var(--ink-light); letter-spacing: .3px;
  }
</style>
</head>
<body>
  <main class="card-set">
    <section class="card card--front" aria-label="Card front">
      <div class="brand-block">
        <span class="brand-dot"></span>
        <span class="brand-name">Vexalund</span>
      </div>
      <p class="address">12, Lotus Enclave, Nashik, 422005, India</p>
      <svg class="divider" width="30" height="170" viewBox="0 0 30 170" aria-hidden="true">
        <line x1="29" y1="0" x2="1" y2="170" stroke="#2f9fd3" stroke-width="1"/>
      </svg>
      <div class="person">
        <p class="person-name"><span class="first">Arjun</span> <span class="rest">K. Malhotra</span></p>
        <p class="person-role">CEO</p>
      </div>
      <ul class="contacts">
        <li>
          <svg viewBox="0 0 14 14" aria-hidden="true"><rect x="3" y="1" width="8" height="12" rx="1.5" fill="none" stroke="#ef5f4c" stroke-width="1.4"/></svg>
          +91 98230 41756
        </li>
        <li>
          <svg viewBox="0 0 14 14" aria-hidden="true"><circle cx="7" cy="7" r="6" fill="#2f9fd3"/><path d="M1 7h12M7 1c-3 3-3 9 0 12M7 1c3 3 3 9 0 12" fill="none" stroke="#1d1d20" stroke-width=".9"/></svg>
          www.vexalund.com
        </li>
        <li>
          <svg viewBox="0 0 14 14" aria-hidden="true"><rect x="1" y="3" width="12" height="9" rx="1" fill="#ef5f4c"/><path d="M1 3l6 5 6-5" fill="none" stroke="#1d1d20" stroke-width="1"/></svg>
          amalhotra@vexalund.com
        </li>
      </ul>
    </section>

    <section class="card card--back" aria-label="Card back">
      <div class="back-brand">
        <span class="brand-dot"></span>
        <span class="brand-name">Vexalund</span>
      </div>
      <p class="tagline">Care for Every Day.</p>
    </section>
  </main>
</body>
</html>
```